Financial Advisor Resource Firm needs business card design

Need business card design for company in Omaha NE called Meridale Circle. We provide resources to financial advisors....workshop programs, retirement analysis, and insurance planning. I would like to see designs that use grays, greens, black, and white colors. The final design should communicate 'collaboration' and be simple yet attractive to financial planning clients. I will attached our logo and another picture of a puzzle piece coming together. I would like the incorporate the puzzle picture somehow, maybe on the back somehow, with color or just the gray scale....OR, the picture be the front of the card with 'Meridale' definition on it (see upload) and then company logo, employee name, title, address on the back (see ppt uploaded). The following disclosure needs to be included somewhere- Advisory services offered through Stonebrook Assets, LLC.
Updates

I uploaded a svg and ai file of the logo

Target Market(s)

Financial planning clients and financial advisors....so pretty diverse age range of about 40-70.

Industry/Entity Type

Financial Planning

Contact Information for Business Card

Tobias L. Fenwright, MBA
Founder/President
5287 E. Larkin Road
Suite 230
Omaha, NE 68190
Phone- (402) 555-0147
Cell- (402) 555-0183
Fax- (402) 555-0129
email- tobias@meridaleplan.example
web address- www.meridaleplan.example

Colors
1b1b1b
474747
d3d3d3
ffffff
9bcb3c
abd036

Requirements
Must have
• Must include logo provided, must be 2 sided, and must have disclosure...all of these items listed in project description

```html
<!DOCTYPE html>
<html lang="en">
<head>
<meta charset="utf-8">
<title>Meridale Circle — Business Card</title>
<link rel="stylesheet" href="https://fonts.googleapis.com/css2?family=Lato:wght@400;700&display=swap">
<style>
  :root {
    --backdrop: #2a2a2a;
    --card: #1b1b1b;
    --rule: #474747;
    --silver: #d3d3d3;
    --white: #ffffff;
    --green: #9bcb3c;
    --green-alt: #abd036;
  }
  * { box-sizing: border-box; margin: 0; padding: 0; }
  html, body { width: 1200px; height: 900px; overflow: hidden; }
  body {
    background: var(--backdrop);
    font-family: "Lato", Arial, sans-serif;
    color: var(--white);
    position: relative;
  }
  .card {
    position: absolute;
    left: 320px;
    width: 560px;
    height: 320px;
    background: var(--card);
    border-radius: 18px;
    box-shadow: 0 12px 30px rgba(0,0,0,.45);
  }
  .card--back { top: 110px; }
  .card--front { top: 470px; }

  /* back */
  .back-brand {
    position: absolute;
    top: 104px; left: 0; right: 0;
    display: flex; align-items: center; justify-content: center; gap: 14px;
  }
  .brand-dot {
    width: 26px; height: 26px; border-radius: 50%;
    background: var(--silver);
  }
  .back-brand .brand-name {
    font-size: 30px; font-weight: 400; letter-spacing: 3px;
    color: var(--silver); text-transform: uppercase;
  }
  .back-rule {
    position: absolute; left: 150px; right: 30px; top: 262px;
    height: 1px; background: var(--rule);
  }
  .disclosure {
    position: absolute; right: 30px; top: 274px;
    font-size: 11px; letter-spacing: .6px; text-transform: uppercase;
    color: var(--silver);
  }

  /* front */
  .front-brand {
    position: absolute; top: 44px; right: 34px;
    font-size: 28px; font-weight: 400; letter-spacing: 3px;
    color: var(--white); text-transform: uppercase;
  }
  .front-rule {
    position: absolute; left: 230px; right: 30px; top: 104px;
    height: 1px; background: var(--rule);
  }
  .person {
    position: absolute; left: 34px; top: 160px;
  }
  .person-name {
    font-size: 18px; font-weight: 700; color: var(--green);
    text-transform: uppercase; letter-spacing: .4px;
  }
  .person-name .credential {
    font-size: 14px; font-weight: 400; letter-spacing: .3px;
  }
  .person-title { font-size: 14px; color: var(--white); margin-top: 1px; }
  .contacts { list-style: none; margin-top: 12px; }
  .contacts li {
    display: flex; align-items: center; gap: 8px;
    font-size: 14px; line-height: 19px; color: var(--white);
  }
  .contacts svg { width: 12px; height: 12px; fill: var(--green); flex: none; }
  .location {
    position: absolute; right: 34px; top: 142px; text-align: right;
  }
  .website { font-size: 14px; color: var(--green); margin-bottom: 10px; }
  .address { font-size: 14px; line-height: 18px; color: var(--white); font-style: normal; }
</style>
</head>
<body>

<section class="card card--back" aria-label="Card back">
  <div class="back-brand">
    <span class="brand-dot"></span>
    <span class="brand-name">Meridale Circle</span>
  </div>
  <div class="back-rule"></div>
  <p class="disclosure">Advisory services offered through Stonebrook Assets, LLC.</p>
</section>

<section class="card card--front" aria-label="Card front">
  <div class="front-brand">Meridale Circle</div>
  <div class="front-rule"></div>

  <div class="person">
    <p class="person-name">Tobias L. Fenwright, <span class="credential">MBA</span></p>
    <p class="person-title">Founder/President</p>
    <ul class="contacts">
      <li>
        <svg viewBox="0 0 12 12" aria-hidden="true"><path d="M1 4c0-2 2-3 5-3s5 1 5 3v1H8V4H4v1H1z M2 6h8l1 5H1z"/></svg>
        (402) 555-0147
      </li>
      <li>
        <svg viewBox="0 0 12 12" aria-hidden="true"><path d="M3 0h6v12H3z M4 1.5v8h4v-8z"/></svg>
        (402) 555-0183
      </li>
      <li>
        <svg viewBox="0 0 12 12" aria-hidden="true"><path d="M3 0h6v4H3z M0 4h12v6H9v2H3v-2H0z M4 8v3h4V8z"/></svg>
        (402) 555-0129
      </li>
      <li>
        <svg viewBox="0 0 12 12" aria-hidden="true"><path d="M0 2h12v8H0z M1 3l5 4 5-4v-.2H1z" fill-rule="evenodd"/></svg>
        tobias@meridaleplan.example
      </li>
    </ul>
  </div>

  <div class="location">
    <p class="website">www.meridaleplan.example</p>
    <address class="address">5287 E. Larkin Road<br>Suite 230 Omaha, NE 68190</address>
  </div>
</section>

</body>
</html>
```